International Trade Consulting Firm Seeks Quality Newsletter Design

Our company provides consulting services to Pinnacle 300 type companies. We compete with the largest consulting companies in the world. However, we have the highest level of expertise in the industry and need to look the most professional and high end. We have very relevant and important information to provide our customers about their compliance and projects. We will have the winning design coded to be an e-newsletter, so it needs to be one page. We want to keep our company colors and logo design in the newsletter, they are attached. We DO NOT want it to look like a mini-version of our website. We want a fresh look to this marketing piece. Newsletter will need to include title, possible sub-heading, space for a feature story, 2 other stories included, and space on either the left or right for short cuts, links or highlights of other articles. Contents/'In this issue' section, about us or branding area, section for relevant links, etc...
Pinnacle 300 companies, High-level management
Marketing

```html
<!DOCTYPE html>
<html lang="en">
<head>
<meta charset="utf-8">
<title>TradeBrief 411 Newsletter</title>
<link rel="stylesheet" href="https://fonts.googleapis.com/css2?family=Roboto+Condensed:wght@400;700&family=Arimo:wght@400;700&display=swap">
<style>
:root{
  --stage:#9a9b9d;
  --paper:#ffffff;
  --ink:#222222;
  --night:#1b1b1b;
  --bar:#3a3a3a;
  --forest:#1f4d22;
  --leaf:#5ea03c;
  --straw:#e9e08c;
  --olive:#9b9a1f;
  --rule:#cdd287;
  --highlight:#fbf5aa;
  --muted:#d8d8d8;
}
*{margin:0;padding:0;box-sizing:border-box}
html,body{width:1200px;height:900px;overflow:hidden}
body{background:var(--stage);font-family:"Arimo",Arial,sans-serif;color:var(--ink);position:relative}
.sheet{position:absolute;top:20px;width:522px;height:880px;background:var(--paper);box-shadow:0 0 6px rgba(0,0,0,.35);overflow:hidden}
.sheet--green{left:63px}
.sheet--gold{left:638px}
.sidebar{position:absolute;left:0;top:0;width:174px;height:880px;border-right:1px solid var(--rule)}
.brand{position:absolute;left:0;top:0;width:174px;height:208px;background:var(--night);padding:38px 22px 0}
.brand-name{font-family:"Roboto Condensed",sans-serif;font-weight:700;font-size:25px;line-height:26px;color:var(--leaf);letter-spacing:1px}
.brand-intro{position:absolute;left:22px;top:132px;width:140px;font-size:9.4px;line-height:15.8px;color:var(--straw)}
.brand-intro u{text-decoration:underline}
.social-bar{position:absolute;top:208px;left:0;width:174px;height:34px;background:var(--bar);display:flex;gap:22px;align-items:center;padding-left:22px}
.social-dot{width:13px;height:13px;border-radius:50%;background:var(--muted)}
.site-link{position:absolute;top:242px;left:0;width:174px;height:28px;line-height:28px;text-align:center;font-weight:700;font-size:10px;letter-spacing:2px;color:#333;border-bottom:1px solid var(--rule)}
.contents{position:absolute;top:270px;left:0;width:174px;height:202px;border-bottom:1px solid var(--rule)}
.contents-item{position:absolute;left:0;width:174px;padding:0 22px}
.contents-item h3{font-family:"Roboto Condensed",sans-serif;font-weight:700;font-size:12.5px;color:var(--forest);line-height:14px}
.contents-item p{font-size:7.4px;line-height:10px;color:#333}
.contents-item--featured{background:var(--highlight);padding-top:8px;height:48px}
.profile{position:absolute;top:494px;left:0;width:174px}
.portrait{position:absolute;left:26px;top:0;width:62px;height:62px;border-radius:50%;border:2px solid #444;background:radial-gradient(circle at 50% 40%,#c9a58a,#8d7768 70%,#e8e6e0)}
.profile-name{position:absolute;left:98px;top:22px;font-family:"Roboto Condensed",sans-serif;font-weight:700;font-size:10.5px;color:var(--forest);line-height:12px}
.profile-role{font-family:"Arimo",sans-serif;font-weight:400;font-size:9px;color:var(--leaf)}
.profile-bio{position:absolute;left:22px;top:76px;width:140px;font-size:9.4px;line-height:15.8px}
.profile-bio p+p{margin-top:16px}
.about{position:absolute;top:765px;left:0;width:174px;height:115px;border-top:1px solid var(--rule);padding:11px 22px}
.about h3{font-family:"Roboto Condensed",sans-serif;font-weight:700;font-size:12.5px;color:var(--forest)}
.about svg{display:block;margin:10px auto 0}
.about h4{font-size:8.6px;font-weight:700;margin-top:10px}
.about p{font-size:8.6px}
.masthead{position:absolute;left:174px;top:0;width:348px;height:208px}
.sheet--green .masthead{background:radial-gradient(ellipse at 80% 0%,#1f4a26 0%,#162a18 45%,#141614 100%)}
.sheet--gold .masthead{background:radial-gradient(ellipse at 95% 5%,#6a5e44 0%,#3c3628 40%,#181716 80%)}
.issue-date{position:absolute;right:22px;top:19px;font-family:"Roboto Condensed",sans-serif;font-weight:700;font-size:9.5px;color:var(--straw)}
.issue-date span{font-weight:400}
.masthead h1{position:absolute;left:16px;top:126px;font-family:"Roboto Condensed",sans-serif;font-weight:700;font-size:35px;color:#fff;letter-spacing:.5px}
.tagline{position:absolute;left:16px;top:175px;display:flex;align-items:center;gap:10px;font-family:"Roboto Condensed",sans-serif;font-size:8.6px;color:#e8e8e8}
.story{position:absolute;left:190px;width:320px}
.story h2{font-family:"Roboto Condensed",sans-serif;font-weight:700;color:var(--forest);letter-spacing:.3px}
.story--lead{top:222px}
.story--lead h2{font-size:36px;line-height:40px}
.story--second{top:490px}
.story--second h2{font-size:27px;line-height:31px}
.subhead{display:flex;align-items:center;gap:8px;margin-top:6px;font-family:"Roboto Condensed",sans-serif;font-weight:700;font-size:10.5px;color:var(--forest)}
.story-body{font-size:10.4px;line-height:18px;margin-top:8px}
.story--second .story-body{margin-top:5px}
.read-more{display:block;margin-top:6px;width:94px;height:22px}
.feature-photo{position:absolute;left:174px;top:765px;width:348px;height:115px;background:linear-gradient(100deg,#c8c0b2 0%,#e9e4dc 35%,#a7937c 60%,#d8cfc2 100%)}
.feature-label{position:absolute;left:16px;bottom:0;background:var(--night);color:var(--straw);font-family:"Arimo",sans-serif;font-size:10.5px;padding:4px 14px 4px 20px}
.corner-star{position:absolute;left:164px;top:751px}
</style>
</head>
<body>

<article class="sheet sheet--green">
  <aside class="sidebar">
    <div class="brand">
      <div class="brand-name">HARBORLINE<br>TRADE</div>
      <p class="brand-intro">Editaquos rem restis dis imoditi ossitat urestius aut aut <u>pariberum</u> faccus <u>doloribus</u> aut prem repedis et eosam fuga.</p>
    </div>
    <div class="social-bar"><span class="social-dot"></span><span class="social-dot"></span><span class="social-dot"></span><span class="social-dot"></span></div>
    <div class="site-link">www.harborlinetrade.com</div>
    <nav class="contents">
      <div class="contents-item" style="top:13px"><h3>ARTICLE 1</h3><p>Editaquos rem restis dis imoditi ossitat<br>aut aut pariberum fuga.</p></div>
      <div class="contents-item" style="top:61px"><h3>ARTICLE 2</h3><p>Editaquos rem restis dis imoditi ossitat<br>aut aut pariberum fuga.</p></div>
      <div class="contents-item contents-item--featured" style="top:104px"><h3>FEATURED STORY</h3><p>Editaquos rem restis dis imoditi ossitat<br>aut aut pariberum fuga.</p></div>
      <div class="contents-item" style="top:160px"><h3>ARTICLE 3</h3><p>Editaquos rem restis dis imoditi ossitat<br>aut aut pariberum fuga.</p></div>
    </nav>
    <section class="profile">
      <div class="portrait" role="img" aria-label="Portrait photo of the CEO"></div>
      <div class="profile-name">DANIEL MARSH<br><span class="profile-role">CEO</span></div>
      <div class="profile-bio">
        <p>Editaquos rem restis dis imoditi ossitat urestius aut aut pariberum faccus doloribus aut prem repedis et eosam fuga. Giam quis quiae vel incid etur?</p>
        <p>Erchiliquo culparciame nobitates ma por rem exerrun tibusti doluptiore dipsuntus Iciendant id quossedit, ius consequia debit alit expellore sin eest vendita sperfernamus autetur?</p>
      </div>
    </section>
    <section class="about">
      <h3>ABOUT US</h3>
      <svg width="40" height="46" viewBox="0 0 40 46" fill="none" stroke="#9b9a1f" stroke-width="2"><path d="M12 2v6M18 2v6M24 2v6"/><path d="M4 16h26v12a11 11 0 0 1-11 11h-4A11 11 0 0 1 4 28z"/><path d="M30 19h3a4 4 0 0 1 0 8h-3"/><path d="M2 43h30"/></svg>
      <h4>OMNIHILLES DERORRO VLAUT</h4>
      <p>Accabor eperum esciasi</p>
    </section>
  </aside>

  <header class="masthead">
    <div class="issue-date">16 APRIL <span>2014</span></div>
    <h1>TRADEBRIEF 411</h1>
    <div class="tagline"><svg width="24" height="8" viewBox="0 0 24 8"><path d="M0 4h22M18 1l4 3-4 3" stroke="#5ea03c" stroke-width="1.5" fill="none"/></svg>YOUR SOURCE FOR THE LATEST IN TRADE ZONE SOFTWARE AND TECHNOLOGY NEWS</div>
  </header>

  <section class="story story--lead">
    <h2>HEADING TITLE OF<br>THE ARTICLE BELOW</h2>
    <p class="story-body">Lendae res nulpa cus, cum fugia volo quodipsus eiciis nullamus invera as et quiataq uoditin velent.<br>Editaquos rem restis dis imoditi ossitat urestius aut aut pariberum faccus doloribus aut prem repedis et eosam fuga. It ipsum et quas dolorporiate natur se dolore eum ent modigen dandand anditate eicat apiet eicit omnis eum, arum evernat emquisti sus.<br>Omnihilles derorro volo conse laut voloreh endite pre illa secabo.</p>
    <svg class="read-more" viewBox="0 0 94 22"><path d="M.5 .5h93v21H.5l6-10.5z" fill="none" stroke="#9b9a1f"/><text x="19" y="15" font-family="Arimo, sans-serif" font-size="10.5" fill="#1f4d22">READ MORE</text></svg>
  </section>

  <section class="story story--second">
    <h2>SMALLER HEADING TITLE<br>FOR LONGER TITLE TEXT</h2>
    <div class="subhead"><svg width="24" height="8" viewBox="0 0 24 8"><path d="M0 4h22M18 1l4 3-4 3" stroke="#7a9a6a" stroke-width="1.5" fill="none"/></svg>HERE IS POSSIBLE SUBHEADING</div>
    <p class="story-body">Lendae res nulpa cus, cum fugia volo quodipsus eiciis nullamus invera as et quiataq uoditin velent.<br>Editaquos rem restis dis imoditi ossitat urestius aut aut pariberum faccus doloribus aut prem repedis et eosam fuga. It ipsum et quas dolorporiate natur se dolore eum ent modigen dandand anditate eicat apiet eicit omnis eum, arum evernat emquisti sus.<br>Omnihilles derorro volo conse laut voloreh endite pre illa secabo.</p>
    <svg class="read-more" viewBox="0 0 94 22"><path d="M.5 .5h93v21H.5l6-10.5z" fill="none" stroke="#9b9a1f"/><text x="19" y="15" font-family="Arimo, sans-serif" font-size="10.5" fill="#1f4d22">READ MORE</text></svg>
  </section>

  <div class="feature-photo" role="img" aria-label="Photo of a team collaborating in a bright office">
    <span class="feature-label">FEATURED STORY</span>
  </div>
  <svg class="corner-star" width="30" height="30" viewBox="0 0 30 30"><path d="M15 1l4 10h10l-8 6 3 11-9-6-9 6 3-11-8-6h10z" fill="#f3ec8a" stroke="#c9c257"/></svg>
</article>

<article class="sheet sheet--gold">
  <aside class="sidebar">
    <div class="brand">
      <div class="brand-name">HARBORLINE<br>TRADE</div>
      <p class="brand-intro">Editaquos rem restis dis imoditi ossitat urestius aut aut <u>pariberum</u> faccus <u>doloribus</u> aut prem repedis et eosam fuga.</p>
    </div>
    <div class="social-bar"><span class="social-dot"></span><span class="social-dot"></span><span class="social-dot"></span><span class="social-dot"></span></div>
    <div class="site-link">www.harborlinetrade.com</div>
    <nav class="contents">
      <div class="contents-item" style="top:13px"><h3>ARTICLE 1</h3><p>Editaquos rem restis dis imoditi ossitat<br>aut aut pariberum fuga.</p></div>
      <div class="contents-item" style="top:61px"><h3>ARTICLE 2</h3><p>Editaquos rem restis dis imoditi ossitat<br>aut aut pariberum fuga.</p></div>
      <div class="contents-item contents-item--featured" style="top:104px"><h3>FEATURED STORY</h3><p>Editaquos rem restis dis imoditi ossitat<br>aut aut pariberum fuga.</p></div>
      <div class="contents-item" style="top:160px"><h3>ARTICLE 3</h3><p>Editaquos rem restis dis imoditi ossitat<br>aut aut pariberum fuga.</p></div>
    </nav>
    <section class="profile">
      <div class="portrait" role="img" aria-label="Portrait photo of the CEO"></div>
      <div class="profile-name">DANIEL MARSH<br><span class="profile-role">CEO</span></div>
      <div class="profile-bio">
        <p>Editaquos rem restis dis imoditi ossitat urestius aut aut pariberum faccus doloribus aut prem repedis et eosam fuga. Giam quis quiae vel incid etur?</p>
        <p>Erchiliquo culparciame nobitates ma por rem exerrun tibusti doluptiore dipsuntus Iciendant id quossedit, ius consequia debit alit expellore sin eest vendita sperfernamus autetur?</p>
      </div>
    </section>
    <section class="about">
      <h3>ABOUT US</h3>
      <svg width="40" height="46" viewBox="0 0 40 46" fill="none" stroke="#9b9a1f" stroke-width="2"><path d="M12 2v6M18 2v6M24 2v6"/><path d="M4 16h26v12a11 11 0 0 1-11 11h-4A11 11 0 0 1 4 28z"/><path d="M30 19h3a4 4 0 0 1 0 8h-3"/><path d="M2 43h30"/></svg>
      <h4>OMNIHILLES DERORRO VLAUT</h4>
      <p>Accabor eperum esciasi</p>
    </section>
  </aside>

  <header class="masthead">
    <div class="issue-date">16 APRIL <span>2014</span></div>
    <h1>TRADEBRIEF 411</h1>
    <div class="tagline"><svg width="24" height="8" viewBox="0 0 24 8"><path d="M0 4h22M18 1l4 3-4 3" stroke="#5ea03c" stroke-width="1.5" fill="none"/></svg>YOUR SOURCE FOR THE LATEST IN TRADE ZONE SOFTWARE AND TECHNOLOGY NEWS</div>
  </header>

  <section class="story story--lead">
    <h2>HEADING TITLE OF<br>THE ARTICLE BELOW</h2>
    <p class="story-body">Lendae res nulpa cus, cum fugia volo quodipsus eiciis nullamus invera as et quiataq uoditin velent.<br>Editaquos rem restis dis imoditi ossitat urestius aut aut pariberum faccus doloribus aut prem repedis et eosam fuga. It ipsum et quas dolorporiate natur se dolore eum ent modigen dandand anditate eicat apiet eicit omnis eum, arum evernat emquisti sus.<br>Omnihilles derorro volo conse laut voloreh endite pre illa secabo.</p>
    <svg class="read-more" viewBox="0 0 94 22"><path d="M.5 .5h93v21H.5l6-10.5z" fill="none" stroke="#9b9a1f"/><text x="19" y="15" font-family="Arimo, sans-serif" font-size="10.5" fill="#1f4d22">READ MORE</text></svg>
  </section>

  <section class="story story--second">
    <h2>SMALLER HEADING TITLE<br>FOR LONGER TITLE TEXT</h2>
    <div class="subhead"><svg width="24" height="8" viewBox="0 0 24 8"><path d="M0 4h22M18 1l4 3-4 3" stroke="#7a9a6a" stroke-width="1.5" fill="none"/></svg>HERE IS POSSIBLE SUBHEADING</div>
    <p class="story-body">Lendae res nulpa cus, cum fugia volo quodipsus eiciis nullamus invera as et quiataq uoditin velent.<br>Editaquos rem restis dis imoditi ossitat urestius aut aut pariberum faccus doloribus aut prem repedis et eosam fuga. It ipsum et quas dolorporiate natur se dolore eum ent modigen dandand anditate eicat apiet eicit omnis eum, arum evernat emquisti sus.<br>Omnihilles derorro volo conse laut voloreh endite pre illa secabo.</p>
    <svg class="read-more" viewBox="0 0 94 22"><path d="M.5 .5h93v21H.5l6-10.5z" fill="none" stroke="#9b9a1f"/><text x="19" y="15" font-family="Arimo, sans-serif" font-size="10.5" fill="#1f4d22">READ MORE</text></svg>
  </section>

  <div class="feature-photo" role="img" aria-label="Photo of a team collaborating in a bright office">
    <span class="feature-label">FEATURED STORY</span>
  </div>
  <svg class="corner-star" width="30" height="30" viewBox="0 0 30 30"><path d="M15 1l4 10h10l-8 6 3 11-9-6-9 6 3-11-8-6h10z" fill="#f3ec8a" stroke="#c9c257"/></svg>
</article>

</body>
</html>
```